Harbor Ledger Funds Bus card and Logo

I need a logo design and Bus card design. The fund focuses on evaluating and investing in minerals (sub-surface rights) and real estate.

Harbor ledger refers to a book of knowledge that each plebe gets when entering the Kelmont Marine Academy (my alma mater)

Target Market(s)

Investors and financial advisors

Contact Information for Business Card

Simple - perhaps a logo with a theme on book of knowledge

Logo Text

Ex Scientia Imperium

Font styles to use
Serif
Sans Serif

Colors

Designer to choose colors to be used in the design.

Requirements
Must have
• memorable logo that is relatively simple

```html
<!DOCTYPE html>
<html lang="en">
<head>
<meta charset="utf-8">
<title>Harbor Ledger Funds – Business Card</title>
<link rel="stylesheet" href="https://fonts.googleapis.com/css2?family=Open+Sans:wght@400;600&family=Roboto:wght@500;700&display=swap">
<style>
  :root {
    --backdrop: #7a7a7a;
    --card-light: #eeeeee;
    --card-dark: #232323;
    --brand-green: #86c440;
    --brand-blue: #3399d1;
    --ink: #1c1c1c;
    --rule: #9a9a9a;
    --wordmark-light: #e6e6e6;
  }
  html, body {
    margin: 0;
    padding: 0;
    width: 1200px;
    height: 1200px;
    overflow: hidden;
    background: var(--backdrop);
  }
  .canvas {
    position: relative;
    width: 1200px;
    height: 1200px;
  }
  .card {
    position: absolute;
    top: 310px;
    height: 594px;
    box-shadow: 2px 3px 6px rgba(0,0,0,0.35);
  }
  .card--front {
    left: 234px;
    width: 364px;
    background: var(--card-light);
    font-family: "Open Sans", Arial, sans-serif;
    color: var(--ink);
    text-align: center;
  }
  .card--back {
    left: 627px;
    width: 370px;
    background: var(--card-dark);
  }
  .brand-block {
    position: absolute;
    left: 0;
    right: 0;
    display: flex;
    flex-direction: column;
    align-items: center;
  }
  .card--front .brand-block { top: 150px; }
  .card--back .brand-block { top: 236px; }
  .brand-dot {
    border-radius: 50%;
    background: var(--brand-blue);
  }
  .card--front .brand-dot { width: 120px; height: 120px; }
  .card--back .brand-dot { width: 96px; height: 96px; }
  .brand-name {
    font-family: "Roboto", Arial, sans-serif;
    font-weight: 500;
    font-size: 29px;
    color: var(--wordmark-light);
    text-transform: uppercase;
    white-space: nowrap;
    margin-top: 30px;
  }
  .contact {
    position: absolute;
    top: 336px;
    left: 0;
    right: 0;
  }
  .contact__name {
    font-family: "Roboto", Arial, sans-serif;
    font-weight: 500;
    font-size: 21px;
    color: var(--brand-green);
    margin: 0;
    line-height: 28px;
    text-transform: uppercase;
  }
  .contact__role {
    font-size: 17px;
    margin: 0;
    line-height: 22px;
  }
  .contact__rule {
    width: 208px;
    height: 1px;
    background: var(--rule);
    margin: 12px auto 8px;
    border: 0;
  }
  .contact__lines {
    list-style: none;
    margin: 0;
    padding: 0;
    font-size: 17px;
    line-height: 21.5px;
  }
  .label { color: var(--brand-green); }
  .web { color: var(--brand-green); }
  .web b { color: var(--brand-blue); font-weight: 400; }
  .address {
    font-size: 17px;
    line-height: 21.5px;
    margin: 0;
  }
</style>
</head>
<body>
<main class="canvas">
  <section class="card card--front">
    <div class="brand-block">
      <div class="brand-dot"></div>
    </div>
    <div class="contact">
      <p class="contact__name">Daniel Morrow</p>
      <p class="contact__role">Managing Director</p>
      <hr class="contact__rule">
      <ul class="contact__lines">
        <li><span class="label">P:</span> 044-555 018 274</li>
        <li><span class="label">M:</span> 044-555 018 391</li>
        <li><span class="label">E:</span> info@harborledger.com</li>
        <li class="web">www.<b>harborledger</b>.com</li>
      </ul>
      <hr class="contact__rule">
      <p class="address">12345, Address Goes Here<br>Country Name, 123456.</p>
    </div>
  </section>

  <section class="card card--back">
    <div class="brand-block">
      <div class="brand-dot"></div>
      <div class="brand-name">Harbor Ledger Funds</div>
    </div>
  </section>
</main>
</body>
</html>
```